institute for female grief councelors needs a design for its facebook group

Each year about 350.000 German women do have a misscarriage while they are pregnant. Their pain and grief is soul deep. Lots of them are stay still in grief even if they have got other children who are healthy and alive. Lots of these women have got difficulty in finally letting go pain, rage and grief. Some are even still in grief after more than twenty or thirty years of having lost their child through misscarriage!!!!

With this facebook group I want to give hope, trust and support as well as helpful advice in coping with this deep soul pain after having lost your child through misscarriage.

The facebook cover shall cause a great curiosity and fascination to the mothers so that they are interested in joining our facebook group.

At our institute women can book a-one-year-training to become a certified "Coach for BirkenFeen" (grief councelor for women who are in deep grief after their misscarriage).

In Germany children who died through misscarriage are named "Sternenkind" (STARCHILD).
Therefore I want to have at least one shing star at the facebook cover symbolizing the still shining soullight of the dead child watching its mother who is still living on earth.

On the left side of the uploaded file you see the planet venus: symbol for mothers / female side of life.
The red sky colour symbolizes the colour of the uterus, the embryo's home before having died through misscarriage.
It ist also possible to include the silhoutte of a mother / several mothers looking up into the red / blue sky to watch the shining soullight of their dead child.

The facebook cover MUST include the following sentence:

Mama, ich lasse mein Licht für dich leuchten

(Mummy, I let my soullight shine for you)

Low design quality

Target Market(s)

German speaking mothers

Industry/Entity Type

coaching

Font styles to use
Script

Colors

Designer to choose colors to be used in the design.

Requirements
Must have
• golden fond writing, at least one shing star, silhouette of one / several mothers (no model typa - normal woman)
Nice to have
• planet venus - red background cover (like uterus colour)
Should not have
• mothers who like like a model or filmstar

```html
<!DOCTYPE html>
<html lang="de">
<head>
<meta charset="utf-8">
<title>Sternenkind – Facebook Titelbild</title>
<link rel="stylesheet" href="https://fonts.googleapis.com/css2?family=Great+Vibes&family=Montserrat:wght@800&display=swap">
<style>
  :root {
    --sky-deep: #120d2a;
    --sky-violet: #3a1d4f;
    --sky-red: #b8323a;
    --glow: #fff3e6;
    --venus-light: #f0dcb0;
    --venus-mid: #d9b97c;
    --venus-warm: #e0a070;
    --silhouette: #050304;
    --text-white: #ffffff;
    --gold: #b38a3e;
    --gold-light: #e6c36a;
    --button-bg: #ffffff;
  }
  * { margin: 0; padding: 0; box-sizing: border-box; }
  html, body { width: 1200px; height: 676px; overflow: hidden; background: var(--sky-deep); }
  .cover {
    position: relative;
    width: 1200px;
    height: 676px;
    overflow: hidden;
  }
  .night-sky {
    position: absolute;
    inset: 0;
    background:
      radial-gradient(circle at 220px 143px, var(--glow) 0, rgba(255,220,200,0.9) 22px, rgba(230,110,90,0.55) 70px, rgba(184,50,58,0.35) 170px, rgba(184,50,58,0) 330px),
      radial-gradient(ellipse at 120px 100px, rgba(184,50,58,0.55), rgba(184,50,58,0) 380px),
      radial-gradient(ellipse at 420px 300px, rgba(110,50,120,0.55), rgba(110,50,120,0) 420px),
      linear-gradient(160deg, var(--sky-violet) 0%, var(--sky-deep) 55%, #0c0a1e 100%);
  }
  .venus {
    position: absolute;
    left: 600px;
    top: 139px;
    width: 454px;
    height: 454px;
    border-radius: 50%;
    background:
      radial-gradient(circle at 20% 55%, rgba(224,160,112,0.7), rgba(224,160,112,0) 30%),
      linear-gradient(170deg, var(--venus-light) 0%, var(--venus-mid) 55%, #c9a56a 100%);
  }
  .mother-child {
    position: absolute;
    left: 760px;
    top: 236px;
    width: 420px;
    height: 440px;
    background: var(--silhouette);
    border-radius: 160px 180px 0 0;
  }
  .headline {
    position: absolute;
    left: 122px;
    top: 168px;
    width: 400px;
    text-align: center;
    font-family: "Great Vibes", cursive;
    font-size: 72px;
    line-height: 77px;
    color: var(--text-white);
    text-shadow: 2px 2px 0 var(--gold);
  }
  .sparkles {
    position: absolute;
    left: 380px;
    top: 150px;
    width: 110px;
    height: 100px;
  }
  .cta {
    position: absolute;
    left: 184px;
    top: 510px;
    display: flex;
    align-items: center;
    gap: 10px;
  }
  .cta-heart { width: 42px; height: 38px; }
  .cta-button {
    display: inline-block;
    background: var(--button-bg);
    color: var(--gold);
    font-family: "Montserrat", sans-serif;
    font-weight: 800;
    font-size: 25px;
    line-height: 42px;
    height: 42px;
    padding: 0 11px;
    border-radius: 10px;
    letter-spacing: 0.3px;
  }
</style>
</head>
<body>
  <main class="cover">
    <div class="night-sky" role="img" aria-label="Sternenhimmel in Violett und Rot mit einem hell leuchtenden Stern oben links"></div>
    <div class="venus" role="img" aria-label="Planet Venus in warmen Gold- und Sandtönen"></div>
    <div class="mother-child" role="img" aria-label="Schwarze Silhouette einer Mutter, die ihr Kind Stirn an Stirn umarmt"></div>

    <h1 class="headline">Mama,<br>ich lasse mein<br>Licht für dich<br>leuchten</h1>

    <svg class="sparkles" viewBox="0 0 110 100" aria-hidden="true">
      <path fill="#ffffff" d="M39 8 C42 30 48 38 72 42 C48 46 42 54 39 76 C36 54 30 46 6 42 C30 38 36 30 39 8 Z"/>
      <path fill="#ffffff" d="M74 15 C75 21 77 23 82 24 C77 25 75 27 74 33 C73 27 71 25 66 24 C71 23 73 21 74 15 Z"/>
      <path fill="#ffffff" d="M90 56 C91 64 94 67 103 69 C94 71 91 74 90 82 C89 74 86 71 77 69 C86 67 89 64 90 56 Z"/>
    </svg>

    <div class="cta">
      <svg class="cta-heart" viewBox="0 0 42 38" aria-hidden="true">
        <defs>
          <linearGradient id="heartGold" x1="0" y1="0" x2="1" y2="1">
            <stop offset="0" stop-color="#e6c36a"/>
            <stop offset="1" stop-color="#a87d32"/>
          </linearGradient>
        </defs>
        <path fill="url(#heartGold)" d="M21 36 C8 27 1 20 1 11 C1 5 6 1 11 1 C15 1 19 3 21 7 C23 3 27 1 31 1 C36 1 41 5 41 11 C41 20 34 27 21 36 Z"/>
      </svg>
      <span class="cta-button">JOIN NOW</span>
    </div>
  </main>
</body>
</html>
```